Animal Horse & Bedding Company Needs a Website Coded & Designed

We need a website for a new animal bedding and feed company that is visually grabbing and vibrant. We would like to see a website that displays trust, quality and confidence. Needs to be responsive and mobile friendly for all browsers and coded for both Android & IOS. SEO is also important.

Joomla or Wordpress – must be both desktop and mobile friendly with fast page load speed. Need the ability to edit ourselves in Wordpress or Joomla.

Full details attached below with some layout and content ideas.

Coding

Coded - Design and coding required

Number of Pages Required

5+ page

Font styles to use
Sans Serif

Requirements
Must have
• Needs to be responsive and mobile friendly for all browsers and coded for both Android & IOS. SEO is also important.

Wordpress – must be both desktop and mobile friendly with fast page load speed. Need the ability to edit ourselves in Wordpress.

Logo Colours:
Dark Brown
CMYK: 50 / 70 / 80 / 70
Pantone: 4625C

Orange
CMYK: 0 / 50 / 100 / 0
Pantone: 144C
Nice to have
• Use picture of building attached and super impose logo on building.

```html
<!DOCTYPE html>
<html lang="en">
<head>
<meta charset="utf-8">
<title>Harvest Loft – Our Feed</title>
<link href="https://fonts.googleapis.com/css2?family=Montserrat:wght@300;400;500;600;700&display=swap" rel="stylesheet">
<style>
:root{
  --orange:#f7941d;
  --orange-soft:#f9a94a;
  --brown:#3b2314;
  --ink:#111111;
  --text:#555555;
  --muted:#8a8a8a;
  --line:#dcdcdc;
  --grey-bg:#f5f5f5;
  --white:#ffffff;
  --star:#f5b400;
}
*{box-sizing:border-box;margin:0;padding:0}
html,body{width:1200px;height:3343px;overflow:hidden}
body{position:relative;font-family:'Montserrat',sans-serif;color:var(--ink);background:var(--white)}
.abs{position:absolute}

/* header */
.site-header{left:0;top:0;width:1200px;height:62px;background:var(--white)}
.brand{left:172px;top:14px;display:flex;align-items:center;gap:10px}
.brand-dot{width:30px;height:30px;border-radius:50%;background:var(--orange)}
.brand-name{font-weight:600;font-size:19px;color:var(--brown);letter-spacing:1px;text-transform:uppercase}
.main-nav a{position:absolute;top:23px;font-size:13px;color:#333;text-decoration:none}
.main-nav a.active{color:var(--orange)}
.main-nav a.active::after{content:"";position:absolute;left:50%;margin-left:-8px;bottom:-9px;width:16px;height:2px;background:var(--orange)}
.btn{display:flex;align-items:center;justify-content:center;background:var(--orange);color:var(--white);font-weight:600;border-radius:3px;text-decoration:none}
.header-quote{left:922px;top:18px;width:105px;height:27px;font-size:13px}

/* hero */
.hero{left:0;top:62px;width:1200px;height:343px;background:linear-gradient(180deg,#3a3f4a 0%,#7a5a45 35%,#d98a3d 55%,#3d4a22 70%,#1f2f12 100%)}
.hero-title{left:172px;top:140px;font-size:47px;font-weight:700;color:var(--white);letter-spacing:-1px}
.hero-text{left:172px;top:214px;width:310px;font-size:15px;line-height:16.5px;color:var(--white)}
.hero-quote{left:172px;top:292px;width:104px;height:26px;font-size:12.5px}

/* intro */
.section-title{left:0;width:1200px;text-align:center;font-size:25px;font-weight:700;letter-spacing:-.5px}
.section-text{left:0;width:1200px;text-align:center;font-size:10px;line-height:15px;color:var(--muted);font-weight:300}
.feed-photo{left:172px;top:616px;width:855px;height:368px;border-radius:4px;background:linear-gradient(120deg,#5d6f80 0%,#3b4a57 35%,#6b5a45 60%,#2b241d 100%)}

/* benefits */
.benefit{width:200px;text-align:center;font-size:12px;font-weight:600;line-height:13px;color:#222}
.benefit svg{display:block;margin:0 auto 8px}

/* products */
.products-band{left:0;top:1414px;width:1200px;height:564px;background:var(--grey-bg)}
.product-card{top:1610px;width:198px;height:271px;background:var(--white);border:1px solid #e6e6e6;border-radius:6px;text-align:center}
.product-shot{position:absolute;left:55px;top:36px;width:88px;height:122px;border-radius:4px;background:linear-gradient(180deg,#e8e8e8 0%,#cfcfcf 55%,#6a4a2a 56%,#8a6238 80%,#d8d8d8 100%)}
.product-name{position:absolute;left:0;top:188px;width:100%;font-size:14px;font-weight:600}
.stars{position:absolute;left:0;top:207px;width:100%;display:flex;justify-content:center;gap:1px}
.price{position:absolute;left:0;top:228px;width:100%;font-size:15px;font-weight:700}
.product-card.hover .overlay{position:absolute;left:14px;top:14px;right:14px;bottom:14px;border-radius:6px;background:var(--orange-soft)}
.product-card.hover .product-name,.product-card.hover .price{color:#fcd6a4}
.zoom{position:absolute;left:50%;top:106px;margin-left:-29px;width:58px;height:58px;border-radius:50%;background:var(--white);display:flex;align-items:center;justify-content:center}
.slider-arrow{top:1737px}

/* quote form */
.quote-box{left:172px;top:2075px;width:855px;height:431px;border:1px solid var(--line);border-radius:8px}
.field{border:1px solid var(--line);border-radius:3px;font-size:9.5px;color:#aaa;padding:0 15px;display:flex;align-items:center;font-weight:300}
.field.area{align-items:flex-start;padding-top:14px}
.send{left:507px;top:2429px;width:197px;height:37px;font-size:13px}

/* testimonials */
.testimonials{left:0;top:2603px;width:1200px;height:419px;background:linear-gradient(100deg,#2c2417 0%,#4a3c27 40%,#3d3220 70%,#2a2214 100%)}
.white{color:var(--white)}
.dot{top:2909px;width:10px;height:10px;border-radius:50%;border:1.5px solid var(--white)}
.dot.on{background:var(--white)}

/* footer */
.site-footer{left:0;top:3022px;width:1200px;height:321px;background:var(--grey-bg)}
.footer-head{font-size:15px;font-weight:500;color:#222}
.footer-small{font-size:9px;line-height:11.5px;color:var(--muted);font-weight:400}
.footer-links a{display:block;font-size:9px;color:var(--muted);text-decoration:none;height:21px}
.social span{display:inline-block;width:9px;height:9px;border-radius:2px;background:var(--orange);margin-right:12px}
.social span.grey{background:#9a9a9a}
.footer-line{left:0;top:3290px;width:1200px;height:1px;background:#bdbdbd}
</style>
</head>
<body>

<header class="site-header abs">
  <div class="brand abs"><span class="brand-dot"></span><span class="brand-name">Harvest Loft</span></div>
  <nav class="main-nav">
    <a style="left:546px">Home</a>
    <a style="left:616px">About Us</a>
    <a style="left:702px" class="active">Feed</a>
    <a style="left:765px">Bedding</a>
    <a style="left:848px">Contact</a>
  </nav>
  <a class="btn header-quote abs">Get a Quote</a>
</header>

<section>
  <div class="hero abs" role="img" aria-label="Tractor and sprayer working a green field at sunset"></div>
  <h1 class="hero-title abs">Our Feed</h1>
  <p class="hero-text abs">Harvest Loft offers supply and delivery of fresh bedding as well as removal of waste bedding.</p>
  <a class="btn hero-quote abs">Get a Quote</a>
</section>

<section>
  <h2 class="section-title abs" style="top:497px">Our Feed</h2>
  <p class="section-text abs" style="top:545px">Hay cubes and pellets are made from premium hay offering a variety of animals a feed that is non-GMO and packed with natural nutrients.<br>These pellets and cubes are less bulky to handle, store and ship. As well, they reduce the amount of wasted feed.</p>
  <div class="feed-photo abs" role="img" aria-label="Farmer pouring a sack of feed into a trough for dairy cows in a barn"></div>
</section>

<section>
  <h2 class="section-title abs" style="top:1036px">Benefits</h2>

  <div class="benefit abs" style="left:170px;top:1108px">
    <svg width="44" height="44" viewBox="0 0 44 44"><circle cx="22" cy="22" r="21" fill="var(--orange)"/><circle cx="22" cy="22" r="15" fill="none" stroke="#fff" stroke-width="1.5"/><text x="22" y="25" font-size="10" font-weight="700" fill="#fff" text-anchor="middle" font-family="Montserrat,sans-serif">100%</text></svg>
    100%<br>Natural
  </div>
  <div class="benefit abs" style="left:392px;top:1108px">
    <svg width="44" height="44" viewBox="0 0 44 44"><path d="M6 40 C2 28 8 16 16 14 L12 6 H26 L22 14 C30 16 34 28 30 40Z" fill="var(--orange)"/><text x="18" y="34" font-size="13" font-weight="700" fill="#fff" text-anchor="middle" font-family="Montserrat,sans-serif">$</text><rect x="32" y="22" width="11" height="3" fill="var(--orange)"/><rect x="32" y="28" width="11" height="3" fill="var(--orange)"/><rect x="32" y="34" width="11" height="3" fill="var(--orange)"/></svg>
    Easy &amp;<br>Cost Effective
  </div>
  <div class="benefit abs" style="left:612px;top:1108px">
    <svg width="48" height="44" viewBox="0 0 48 44"><path d="M4 10 L24 2 L44 10 L24 18Z M4 14 L24 22 L44 14 L44 34 L24 42 L4 34Z" fill="var(--orange)"/><path d="M12 28 L24 32 L36 28" stroke="#fff" stroke-width="3" fill="none"/></svg>
    Available in<br>Pellets or Cubes
  </div>
  <div class="benefit abs" style="left:829px;top:1108px">
    <svg width="44" height="48" viewBox="0 0 44 48"><rect x="13" y="4" width="18" height="6" rx="1" fill="var(--orange)"/><rect x="9" y="12" width="26" height="32" rx="4" fill="var(--orange)"/><rect x="9" y="20" width="26" height="14" fill="#fff"/><path d="M24 22 L18 28 H22 L20 33 L26 27 H22Z" fill="var(--orange)"/></svg>
    High Protein<br>Content
  </div>

  <div class="benefit abs" style="left:170px;top:1233px">
    <svg width="44" height="44" viewBox="0 0 44 44"><rect x="4" y="4" width="12" height="10" fill="var(--orange)"/><rect x="8" y="16" width="4" height="8" fill="var(--orange)"/><rect x="2" y="26" width="16" height="16" fill="var(--orange)"/><path d="M22 4 H42 L36 20 H28Z" fill="var(--orange)"/><rect x="30" y="20" width="4" height="22" fill="var(--orange)"/></svg>
    Eliminates Dust From<br>Feeding Baled Hay
  </div>
  <div class="benefit abs" style="left:392px;top:1233px">
    <svg width="46" height="46" viewBox="0 0 46 46"><circle cx="23" cy="23" r="20" fill="none" stroke="var(--orange)" stroke-width="4"/><circle cx="23" cy="23" r="9" fill="var(--orange)"/><line x1="9" y1="37" x2="37" y2="9" stroke="var(--orange)" stroke-width="4"/></svg>
    Chemical &amp;<br>Additive Free
  </div>
  <div class="benefit abs" style="left:612px;top:1233px">
    <svg width="40" height="46" viewBox="0 0 40 46"><rect x="4" y="4" width="32" height="6" fill="var(--orange)"/><path d="M6 12 H34 L31 44 H9Z" fill="var(--orange)"/><path d="M14 26 A6 6 0 0 1 26 26 M26 30 A6 6 0 0 1 14 30" stroke="#fff" stroke-width="2.5" fill="none"/></svg>
    Less<br>Wasted Feed
  </div>
  <div class="benefit abs" style="left:829px;top:1233px">
    <svg width="44" height="46" viewBox="0 0 44 46"><path d="M16 4 L22 12 L28 4 L26 14 C38 18 42 30 38 42 H6 C2 30 6 18 18 14Z" fill="var(--orange)"/><circle cx="22" cy="30" r="6" fill="#fff"/></svg>
    Eliminate<br>Waste In Feeding
  </div>
</section>

<section>
  <div class="products-band abs"></div>
  <h2 class="section-title abs" style="top:1505px">Our Feed</h2>
  <p class="section-text abs" style="top:1554px">Hay cubes and pellets are made from premium hay offering a variety of animals a feed that is non-GMO and packed with natural nutrients.&nbsp; These pellets and cubes are less<br>bulky to handle, store and ship. As well, they reduce the amount of wasted feed.</p>

  <svg class="slider-arrow abs" style="left:112px" width="10" height="16" viewBox="0 0 10 16"><path d="M8 1 L2 8 L8 15" stroke="#bbb" stroke-width="1.5" fill="none"/></svg>
  <svg class="slider-arrow abs" style="left:1078px" width="10" height="16" viewBox="0 0 10 16"><path d="M2 1 L8 8 L2 15" stroke="#bbb" stroke-width="1.5" fill="none"/></svg>

  <div class="product-card abs" style="left:172px">
    <div class="product-shot" role="img" aria-label="Feed pellet bag"></div>
    <div class="product-name">Product Name</div>
    <div class="stars"><svg width="64" height="11" viewBox="0 0 64 11"><g fill="var(--star)"><polygon points="5.5,0 7,4 11,4 8,6.5 9,10.5 5.5,8 2,10.5 3,6.5 0,4 4,4"/><polygon transform="translate(13 0)" points="5.5,0 7,4 11,4 8,6.5 9,10.5 5.5,8 2,10.5 3,6.5 0,4 4,4"/><polygon transform="translate(26 0)" points="5.5,0 7,4 11,4 8,6.5 9,10.5 5.5,8 2,10.5 3,6.5 0,4 4,4"/><polygon transform="translate(39 0)" points="5.5,0 7,4 11,4 8,6.5 9,10.5 5.5,8 2,10.5 3,6.5 0,4 4,4"/><polygon transform="translate(52 0)" points="5.5,0 7,4 11,4 8,6.5 9,10.5 5.5,8 2,10.5 3,6.5 0,4 4,4"/></g></svg></div>
    <div class="price">$100.00</div>
  </div>
  <div class="product-card abs" style="left:390px">
    <div class="product-shot" role="img" aria-label="Feed pellet bag"></div>
    <div class="product-name">Product Name</div>
    <div class="stars"><svg width="64" height="11" viewBox="0 0 64 11"><g fill="var(--star)"><polygon points="5.5,0 7,4 11,4 8,6.5 9,10.5 5.5,8 2,10.5 3,6.5 0,4 4,4"/><polygon transform="translate(13 0)" points="5.5,0 7,4 11,4 8,6.5 9,10.5 5.5,8 2,10.5 3,6.5 0,4 4,4"/><polygon transform="translate(26 0)" points="5.5,0 7,4 11,4 8,6.5 9,10.5 5.5,8 2,10.5 3,6.5 0,4 4,4"/><polygon transform="translate(39 0)" points="5.5,0 7,4 11,4 8,6.5 9,10.5 5.5,8 2,10.5 3,6.5 0,4 4,4"/><polygon transform="translate(52 0)" points="5.5,0 7,4 11,4 8,6.5 9,10.5 5.5,8 2,10.5 3,6.5 0,4 4,4"/></g></svg></div>
    <div class="price">$100.00</div>
  </div>
  <div class="product-card hover abs" style="left:612px">
    <div class="overlay"></div>
    <div class="zoom"><svg width="26" height="26" viewBox="0 0 26 26"><circle cx="11" cy="11" r="8" fill="none" stroke="var(--orange)" stroke-width="2.2"/><line x1="17" y1="17" x2="24" y2="24" stroke="var(--orange)" stroke-width="2.5"/><line x1="7" y1="11" x2="15" y2="11" stroke="var(--orange)" stroke-width="2"/><line x1="11" y1="7" x2="11" y2="15" stroke="var(--orange)" stroke-width="2"/></svg></div>
    <div class="product-name">Product Name</div>
    <div class="stars"><svg width="64" height="11" viewBox="0 0 64 11"><g fill="#fcc77f"><polygon points="5.5,0 7,4 11,4 8,6.5 9,10.5 5.5,8 2,10.5 3,6.5 0,4 4,4"/><polygon transform="translate(13 0)" points="5.5,0 7,4 11,4 8,6.5 9,10.5 5.5,8 2,10.5 3,6.5 0,4 4,4"/><polygon transform="translate(26 0)" points="5.5,0 7,4 11,4 8,6.5 9,10.5 5.5,8 2,10.5 3,6.5 0,4 4,4"/><polygon transform="translate(39 0)" points="5.5,0 7,4 11,4 8,6.5 9,10.5 5.5,8 2,10.5 3,6.5 0,4 4,4"/><polygon transform="translate(52 0)" points="5.5,0 7,4 11,4 8,6.5 9,10.5 5.5,8 2,10.5 3,6.5 0,4 4,4"/></g></svg></div>
    <div class="price">$100.00</div>
  </div>
  <div class="product-card abs" style="left:830px">
    <div class="product-shot" role="img" aria-label="Feed pellet bag"></div>
    <div class="product-name">Product Name</div>
    <div class="stars"><svg width="64" height="11" viewBox="0 0 64 11"><g fill="var(--star)"><polygon points="5.5,0 7,4 11,4 8,6.5 9,10.5 5.5,8 2,10.5 3,6.5 0,4 4,4"/><polygon transform="translate(13 0)" points="5.5,0 7,4 11,4 8,6.5 9,10.5 5.5,8 2,10.5 3,6.5 0,4 4,4"/><polygon transform="translate(26 0)" points="5.5,0 7,4 11,4 8,6.5 9,10.5 5.5,8 2,10.5 3,6.5 0,4 4,4"/><polygon transform="translate(39 0)" points="5.5,0 7,4 11,4 8,6.5 9,10.5 5.5,8 2,10.5 3,6.5 0,4 4,4"/><polygon transform="translate(52 0)" points="5.5,0 7,4 11,4 8,6.5 9,10.5 5.5,8 2,10.5 3,6.5 0,4 4,4"/></g></svg></div>
    <div class="price">$100.00</div>
  </div>
</section>

<section>
  <div class="quote-box abs"></div>
  <h2 class="section-title abs" style="top:2110px">Request a Quote</h2>
  <div class="field abs" style="left:210px;top:2170px;width:382px;height:37px">First Name*</div>
  <div class="field abs" style="left:608px;top:2170px;width:382px;height:37px">Last Name*</div>
  <div class="field abs" style="left:210px;top:2219px;width:382px;height:38px">Email Address*</div>
  <div class="field abs" style="left:608px;top:2219px;width:382px;height:38px">Contact Number*</div>
  <div class="field area abs" style="left:210px;top:2270px;width:780px;height:139px">Requirements*</div>
  <a class="btn send abs">Send Message</a>
</section>

<section>
  <div class="testimonials abs" role="img" aria-label="Young lambs standing in a field, darkened backdrop"></div>
  <h2 class="section-title white abs" style="top:2701px">Whats Our Clients Says</h2>
  <div class="abs white" style="left:0;top:2762px;width:1200px;text-align:center;font-size:15px;font-weight:600">Daniel Mercer</div>
  <div class="abs white" style="left:0;top:2783px;width:1200px;text-align:center;font-size:10px">Managing Member, Ridgeway Farm Holdings</div>
  <p class="abs white" style="left:300px;top:2818px;width:600px;text-align:center;font-size:10px;line-height:15px">Lorem Ipsum is simply dummy text of the printing and typesetting industry. Lorem Ipsum has been the industry's standard dummy text ever since the 1500s, when an unknown printer took a galley of type and scrambled it to make a type specimen book. It has survived not only five centuries, but also the leap into electronic typesetting, remaining essentially unchanged.</p>
  <svg class="abs" style="left:246px;top:2838px" width="10" height="16" viewBox="0 0 10 16"><path d="M8 1 L2 8 L8 15" stroke="#fff" stroke-width="1.5" fill="none"/></svg>
  <svg class="abs" style="left:944px;top:2838px" width="10" height="16" viewBox="0 0 10 16"><path d="M2 1 L8 8 L2 15" stroke="#fff" stroke-width="1.5" fill="none"/></svg>
  <span class="dot abs" style="left:579px"></span>
  <span class="dot abs" style="left:595px"></span>
  <span class="dot on abs" style="left:611px"></span>
</section>

<footer>
  <div class="site-footer abs"></div>
  <div class="brand abs" style="top:3124px"><span class="brand-dot" style="width:26px;height:26px"></span><span class="brand-name" style="font-size:16px">Harvest Loft</span></div>
  <p class="footer-small abs" style="left:172px;top:3188px;width:160px">Ready to start a new project or curious about our process? Drop us a note or give us a call. We are happy to answer any questions and provide a free consultation.</p>

  <div class="footer-head abs" style="left:433px;top:3108px">Menu</div>
  <nav class="footer-links abs" style="left:435px;top:3146px">
    <a>Home</a><a>About us</a><a>Feed</a><a>Badding</a><a>Contact</a>
  </nav>

  <div class="footer-head abs" style="left:603px;top:3108px">Contact Us</div>
  <p class="footer-small abs" style="left:604px;top:3146px;width:130px">Harvest Loft<br>18 Millbrook Rd #210, Fairview, MA 01990</p>
  <p class="footer-small abs" style="left:604px;top:3192px">555-014-2738</p>
  <p class="footer-small abs" style="left:604px;top:3214px">hello@harvestloft.com</p>

  <div class="footer-head abs" style="left:830px;top:3108px">Social Media</div>
  <div class="social abs" style="left:831px;top:3143px"><span class="grey"></span><span></span><span class="grey"></span><span class="grey"></span><span class="grey"></span></div>
  <div class="abs" style="left:830px;top:3177px;width:197px;height:27px;background:#fff;display:flex;align-items:center;padding-left:12px;gap:10px;font-size:8.5px;color:#aaa">
    <svg width="10" height="8" viewBox="0 0 10 8"><rect width="10" height="8" rx="1" fill="var(--orange)"/></svg>Email Address
  </div>
  <a class="btn abs" style="left:830px;top:3210px;width:197px;height:28px;font-size:9px">Subscribe Now</a>

  <div class="footer-line abs"></div>
  <div class="abs" style="left:0;top:3312px;width:1200px;text-align:center;font-size:8.5px;color:#444">©2021 harvestloft. All Rights Reserved.</div>
</footer>

</body>
</html>
```